Consultancy Business Card Design

We need a business card design for a new company based in singapore called KestrelOak. KestrelOak a boutique consultancy firm offering broad-based business solutions, from conception to re-invention, for ventures from new start-ups to long-running traditional businesses.
Its 2 main divisions (Food & Beverage Operations and Construction & Project Management) have access to a wide range of networks, knowledge bases, and resources to service its clients across numerous diverse sectors. This includes, and is not limited to, construction, F&B, and retail.
We are a company that combines the ambition, boldness and energy of one in the 20s with the dedication, level-headedness and dependability of one entering its 30s. Bridging the experiences of the old with ideals of the young, we draw on the positives of both to create a unique synergy.
We hope to see designs that fits our company profile.
Industry/Entity Type
Boutique
Contact Information for Business Card
KestrelOak(Company Name)
Marcus Thiel (Name)
Principle Consultant (Title)
F&B and Hospitality (Division)
(+65) 8043 5617 (Contact no.)
marcus@kestreloak.com.sg (Email)
Colors
Designer to choose colors to be used in the design.

```html
<!DOCTYPE html>
<html lang="en">
<head>
<meta charset="utf-8">
<title>KestrelOak Business Card</title>
<link rel="stylesheet" href="https://fonts.googleapis.com/css2?family=Anton&family=Open+Sans:wght@400;600&display=swap">
<style>
  :root {
    --backdrop: #3a3b3e;
    --card-white: #ffffff;
    --ink: #262626;
    --band-dark: #55575a;
    --band-light: #c9cacb;
    --accent-green: #a6d65a;
    --text-light: #ffffff;
    --text-dark: #333436;
  }
  * { margin: 0; padding: 0; box-sizing: border-box; }
  html, body {
    width: 1200px;
    height: 900px;
    overflow: hidden;
    background: var(--backdrop);
  }
  .canvas {
    position: relative;
    width: 1200px;
    height: 900px;
  }
  .card {
    position: absolute;
    width: 560px;
    height: 320px;
    background: var(--card-white);
    overflow: hidden;
    box-shadow: 0 10px 30px rgba(0,0,0,0.35);
  }
  .card--front { left: 60px; top: 90px; }
  .card--back { left: 580px; top: 490px; }

  .wordmark {
    position: absolute;
    display: flex;
    align-items: center;
    gap: 12px;
    font-family: "Anton", sans-serif;
    color: var(--ink);
    letter-spacing: -1px;
    line-height: 1;
    text-transform: uppercase;
  }
  .wordmark__square {
    display: block;
    background: var(--accent-green);
  }
  .card--front .wordmark {
    left: 50%;
    top: 50%;
    transform: translate(-50%, -50%);
    font-size: 72px;
  }
  .card--front .wordmark__square { width: 44px; height: 44px; }
  .card--back .wordmark {
    left: 95px;
    top: 36px;
    font-size: 56px;
  }
  .card--back .wordmark__square { width: 34px; height: 34px; }

  .card__bands {
    position: absolute;
    left: 0;
    top: 0;
    width: 560px;
    height: 320px;
  }
  .identity {
    position: absolute;
    left: 24px;
    top: 160px;
    color: var(--text-light);
    font-family: "Open Sans", sans-serif;
    font-variant: small-caps;
    line-height: 1.05;
  }
  .identity__name {
    font-size: 24px;
    font-weight: 600;
  }
  .identity__role {
    font-size: 16px;
    font-weight: 400;
  }
  .contact {
    position: absolute;
    display: flex;
    align-items: center;
    gap: 10px;
    font-family: "Open Sans", sans-serif;
    font-size: 16px;
    color: var(--text-dark);
    letter-spacing: 0.5px;
  }
  .contact svg { flex: none; }
  .contact--phone { left: 262px; top: 178px; }
  .contact--email { left: 232px; top: 258px; }
</style>
</head>
<body>
<main class="canvas">

  <section class="card card--front" aria-label="Business card front">
    <div class="wordmark">
      <span class="wordmark__square" aria-hidden="true"></span>
      <span class="wordmark__name">KestrelOak</span>
    </div>
  </section>

  <section class="card card--back" aria-label="Business card back">
    <div class="wordmark">
      <span class="wordmark__square" aria-hidden="true"></span>
      <span class="wordmark__name">KestrelOak</span>
    </div>

    <svg class="card__bands" viewBox="0 0 560 320" aria-hidden="true">
      <polygon points="0,152 560,124 560,320 0,320" fill="var(--band-dark)"/>
      <polygon points="228,170 560,143 560,320 150,320" fill="var(--card-white)"/>
      <polygon points="234,172 560,147 560,320 158,320" fill="var(--band-light)"/>
      <polygon points="0,252 560,208 560,218 0,262" fill="var(--accent-green)"/>
    </svg>

    <div class="identity">
      <p class="identity__name">Marcus Thiel</p>
      <p class="identity__role">Principle Consultant</p>
      <p class="identity__role">F&amp;B and Hospitality</p>
    </div>

    <p class="contact contact--phone">
      <svg width="16" height="16" viewBox="0 0 24 24" aria-hidden="true">
        <path fill="var(--text-dark)" d="M6.6 10.8a15.1 15.1 0 0 0 6.6 6.6l2.2-2.2c.3-.3.7-.4 1-.2 1.1.4 2.3.6 3.6.6.6 0 1 .4 1 1V20c0 .6-.4 1-1 1A17 17 0 0 1 3 4c0-.6.4-1 1-1h3.5c.6 0 1 .4 1 1 0 1.3.2 2.5.6 3.6.1.3 0 .7-.2 1z"/>
      </svg>
      <span>(+65) 8043 5617</span>
    </p>

    <p class="contact contact--email">
      <svg width="20" height="14" viewBox="0 0 20 14" aria-hidden="true">
        <rect x="0.75" y="0.75" width="18.5" height="12.5" fill="none" stroke="var(--text-dark)" stroke-width="1.5"/>
        <polyline points="1,1 10,8 19,1" fill="none" stroke="var(--text-dark)" stroke-width="1.5"/>
      </svg>
      <span>marcus@kestreloak.com.sg</span>
    </p>
  </section>

</main>
</body>
</html>
```